GearHive.com

Our company, GearHive Inc., is an established business with an extensive worldwide customer base in the Aviation, Aerospace, and Defense Industries.
GearHive Inc, is an e-commerce platform driven by an aviation parts locator. We are looking to totally redo our homepage, log-in page, standard part search page, and results page.
Our current web design is in 800frame and we need it to be updated to a centered 1280 frame. The new design also needs to be easily viewed from any mobile device. The new size needs to accommodate 2-3 advertisements, both vertically and horizontally.
I like clean, simple, crisp lines that can easily be navigated by everyone. Along with Aviation/Aerospace stock photos, I would like to use different shades of blue and grey and accent specific buttons/drop-downs with orange or yellow.
We are also looking for a web designer who also has the ability to cut up the page and turn over to our .NET developers.
Attached are the 4 pages that I would like to start working on. The standard content within these pages need to be incorporated into the new design.
Our current website is www.gearhive.com
Below are some industry websites that I like the color and feel of.
Please use attached pic of corvane T410 as main photo
http://www.stravelcorp.com/
http://www.quillanor.com/en/aerospace.html
http://www.dexavend.com/
http://aerospace.veltrimax.com/

```html
<!DOCTYPE html>
<html lang="en">
<head>
<meta charset="utf-8">
<title>GearHive.com</title>
<link rel="stylesheet" href="https://fonts.googleapis.com/css2?family=Mulish:ital,wght@0,400;0,600;0,700;0,800;1,400&display=swap">
<style>
:root{
  --blue:#1b8ae2;
  --blue-dark:#2b2fa6;
  --navy:#1f2070;
  --link:#1272c9;
  --text:#555;
  --heading:#222;
  --rule:#e2e2e2;
}
*{box-sizing:border-box;margin:0;padding:0}
html,body{width:956px;height:1200px;overflow:hidden;background:#fff;font-family:"Mulish",Arial,sans-serif;color:var(--text)}
.page{position:relative;width:956px;height:1200px}
.header{position:absolute;left:0;top:0;width:956px;height:131px;background:linear-gradient(#fff 40%,#e6e6e6)}
.brand{position:absolute;left:108px;top:30px;font-weight:800;font-size:38px;color:var(--blue);letter-spacing:-1px}
.search{position:absolute;left:664px;top:53px;width:187px;height:24px;border:1px solid #d6d6d6;background:#fff;border-radius:2px;font-size:10px;font-style:italic;color:#999;padding:5px 9px}
.search svg{position:absolute;right:6px;top:4px}
.hero{position:absolute;left:0;top:131px;width:956px;height:403px;background:linear-gradient(#3d7fc6 0%,#8fb8de 45%,#c9d3da 62%,#8a8f92 100%)}
.nav-main{position:absolute;left:105px;top:91px;width:746px;height:39px;background:var(--blue);display:flex}
.nav-main a{flex:auto;color:#fff;text-decoration:none;font-size:14px;font-weight:600;display:flex;align-items:center;justify-content:center;border-right:1px solid rgba(255,255,255,.25)}
.nav-main a:last-child{border:0}
.nav-sub{position:absolute;left:105px;top:130px;width:746px;height:32px;background:var(--blue-dark);display:flex;justify-content:space-around;align-items:center;padding:0 14px}
.nav-sub a{color:#fff;text-decoration:none;font-size:10.5px;font-weight:600}
.caption{position:absolute;left:103px;top:310px;width:339px;height:99px;background:rgba(25,30,40,.82);color:#fff;padding:24px 20px}
.caption .kicker{font-size:12.5px;font-weight:600}
.caption .title{font-size:23px;font-weight:700;margin-top:4px}
.dots{position:absolute;left:103px;top:418px;display:flex;gap:4px}
.dots span{width:10px;height:10px;background:#fff}
.dots span.on{background:var(--blue);border:2px solid #fff}
.photo{position:absolute}
.feature h2{position:absolute;font-size:16px;font-weight:600;color:var(--link)}
.feature p{position:absolute;font-size:9.3px;line-height:14.5px;width:245px}
.btn{position:absolute;width:91px;height:27px;background:var(--blue-dark);color:#fff;font-size:10px;font-weight:700;display:flex;align-items:center;justify-content:center;border-radius:3px}
.solutions{position:absolute;left:633px;top:565px;width:218px;height:221px;border:1px solid #ddd;background:linear-gradient(#fff 70%,#f3f3f3);padding:18px 0 0 23px}
.solutions h3{font-size:16.5px;font-weight:400;color:var(--heading);margin-bottom:10px}
.solutions h4{font-size:11px;font-weight:600;color:var(--link);margin:0 0 4px 3px}
.solutions ul{list-style:none;margin:0 0 13px 3px}
.solutions li{font-size:9.3px;color:#333;line-height:14.6px;padding-left:11px;position:relative}
.solutions li::before{content:"";position:absolute;left:0;top:4px;border-left:4px solid #999;border-top:3px solid transparent;border-bottom:3px solid transparent}
.rule{position:absolute;left:105px;top:832px;width:746px;height:1px;background:var(--rule)}
.section-title{position:absolute;font-size:16px;font-weight:600}
.news{position:absolute;top:898px;width:153px;height:146px;background:var(--blue);color:#fff}
.news .img{height:86px}
.news .date{font-size:9.5px;margin:10px 0 0 13px}
.news .head{font-size:9.4px;font-weight:700;margin:3px 4px 0 13px;line-height:13px;letter-spacing:-.15px}
.testimonial{position:absolute;left:645px;top:898px;width:212px}
.quote{position:relative;font-size:8.9px;font-style:italic;line-height:16px;color:#444;letter-spacing:-.1px}
.qmark{font-size:18px;color:#6e7ad0;font-weight:800;font-style:normal;line-height:0}
.qmark.open{position:absolute;left:-18px;top:8px}
.author{margin-top:8px;font-size:10px;color:#333}
.author em{display:block;color:#555;margin-top:4px}
.footer{position:absolute;left:0;top:1102px;width:956px;height:98px;background:var(--navy);color:#fff}
.footer .links{position:absolute;left:106px;top:26px;font-size:10px;font-weight:700}
.footer .links span{margin:0 4px}
.footer .legal{position:absolute;left:106px;top:50px;font-size:9px}
.social{position:absolute;left:745px;top:21px;display:flex;gap:4px}
.social i{width:21px;height:21px;border-radius:50%;background:#fff;display:block}
</style>
</head>
<body>
<div class="page">
  <header class="header">
    <div class="brand">GearHive</div>
    <div class="search">Search here..
      <svg width="14" height="14" viewBox="0 0 14 14"><circle cx="6" cy="6" r="4.5" fill="none" stroke="#888" stroke-width="1.6"/><line x1="9.3" y1="9.3" x2="13" y2="13" stroke="#888" stroke-width="1.8"/></svg>
    </div>
  </header>
  <div class="hero" role="img" aria-label="Front view of a white passenger jet on the runway under a blue sky"></div>
  <nav class="nav-main">
    <a href="#">GEARHIVE MAIN</a><a href="#">AERO PAGES</a><a href="#">MESSAGE BOARD</a><a href="#">CONTACT</a><a href="#">LOG IN</a>
  </nav>
  <nav class="nav-sub">
    <a href="#">HOME</a><a href="#">ABOUT</a><a href="#">MEMBERSHIP</a><a href="#">BUYERS</a><a href="#">SUPPLIERS</a><a href="#">GOVERNMENT DATA</a><a href="#">MEDA</a><a href="#">FAQ'S</a>
  </nav>
  <div class="caption">
    <div class="kicker">ETIAM EST NUNC VENENATIS TRISTIQUE</div>
    <div class="title">MAURIS VEL LACUS VITAE</div>
  </div>
  <div class="dots"><span class="on"></span><span></span><span></span><span></span></div>

  <section class="feature">
    <div class="photo" style="left:105px;top:565px;width:242px;height:100px;background:linear-gradient(#7fa8cf,#6b6f78)" role="img" aria-label="Two pilots in a cockpit giving thumbs up"></div>
    <h2 style="left:106px;top:673px">INDUSTRY CONNECTIONS</h2>
    <p style="left:106px;top:697px">Etiam est nunc venenatis in tristique eu imperdiet ac nisl Cum sociis natoque penatibus et magnis dis parturient montes nascetur ridiculus</p>
    <div class="btn" style="left:105px;top:749px">READ MORE</div>

    <div class="photo" style="left:371px;top:565px;width:242px;height:100px;background:linear-gradient(#2f7ed4,#9cc4ea)" role="img" aria-label="Hand holding a small toy plane against the sky"></div>
    <h2 style="left:373px;top:673px">OUR COMMUNITY</h2>
    <p style="left:373px;top:697px">Etiam est nunc venenatis in tristique eu imperdiet ac nisl Cum sociis natoque penatibus et magnis dis parturient montes nascetur ridiculus mus In iaculis facilisis</p>
    <div class="btn" style="left:374px;top:749px">READ MORE</div>
  </section>

  <aside class="solutions">
    <h3>OUR SOLUTIONS</h3>
    <h4>Buyer Solutions</h4>
    <ul><li>Parts Search</li><li>Alternative Part Numbers</li><li>Batch Search</li><li>Request for Quotes</li><li>Quality of Search Service</li></ul>
    <h4>Supplier Solutions</h4>
    <ul><li>List Parts</li><li>Overhaul Capabilities</li></ul>
  </aside>

  <div class="rule"></div>

  <h2 class="section-title" style="left:104px;top:868px;color:var(--heading)">MEDIA &amp; NEWS</h2>
  <article class="news" style="left:105px"><div class="img" style="background:linear-gradient(#7d9cc0,#8d8a84)" role="img" aria-label="Business jet parked on the tarmac"></div><div class="date">Jun, 25, 2015</div><div class="head">Agnis dis parturient montes nascetur ridiculus</div></article>
  <article class="news" style="left:274px"><div class="img" style="background:linear-gradient(#8aa6c6,#d9b48a)" role="img" aria-label="Airliner landing over runway lights"></div><div class="date">Jun, 25, 2015</div><div class="head">Agnis dis parturient montes nascetur ridiculus</div></article>
  <article class="news" style="left:443px"><div class="img" style="background:linear-gradient(#5b6470,#9aa2aa)" role="img" aria-label="Aircraft under maintenance in a hangar"></div><div class="date">Jun, 25, 2015</div><div class="head">Agnis dis parturient montes nascetur ridiculus</div></article>

  <h2 class="section-title" style="left:643px;top:867px;color:var(--blue-dark);font-weight:400;font-size:16.5px">TESTIMONIALS</h2>
  <div class="testimonial">
    <p class="quote"><span class="qmark open">&ldquo;</span>Suspendisse vulputate aliquam dui Nulla elementum dui ut augue Aliquam vehicula mi at mauris Maecenas placerat nisl at consequat rhoncus sem nunc gravida justo quis eleifend arcu velit quis lacus Morbi magna magna tinci-dunt a mattis non imperdiet vitae tellus <span class="qmark">&rdquo;</span></p>
    <div class="author">By Author Name<em>Location, City</em></div>
  </div>

  <footer class="footer">
    <div class="links">HOME<span>/</span> ABOUT<span>/</span> MEMBERSHIP<span>/</span> BUYERS<span>/</span> SUPPLIERS<span>/</span> GOVERNMENT DATA<span>/</span> MEDA<span>/</span> FAQ'S</div>
    <div class="legal">© 2014 Company Name &nbsp;All right reserved &nbsp;Term of Use</div>
    <div class="social"><i></i><i></i><i></i><i></i></div>
  </footer>
</div>
</body>
</html>
```